Corvane Capital Business Cards

These are professional business cards that are for my family office.
Put fake emails and phone numbers as of now until I finalize those components. This family office controls my families investments, assets, and future. The cards should be professional.
..
.
.
.
I just uploaded another variation of a logo I would like to see as a business card to I am inbeteen which logo to use

Target Market(s)

business

Industry/Entity Type

business

Contact Information for Business Card

Professional, wealth related, finance related.

Requirements
Must have
• Logo

```html
<!DOCTYPE html>
<html lang="en">
<head>
<meta charset="utf-8">
<title>Corvane Capital Business Cards</title>
<link href="https://fonts.googleapis.com/css2?family=Cinzel:wght@400;600;700&display=swap" rel="stylesheet">
<style>
  :root {
    --backdrop: #2f2f31;
    --card-front: #ffffff;
    --card-back: #a9a9a9;
    --ink: #1c1f2e;
    --ink-soft: #2a2d3a;
    --watermark: #ececec;
    --white: #ffffff;
  }
  * { margin: 0; padding: 0; box-sizing: border-box; }
  html, body {
    width: 1200px;
    height: 1059px;
    overflow: hidden;
    background: var(--backdrop);
    font-family: "Cinzel", serif;
  }
  .stage { position: relative; width: 1200px; height: 1059px; }

  .card {
    position: absolute;
    border-radius: 24px;
    overflow: hidden;
  }
  .card--front {
    left: 256px; top: 100px; width: 688px; height: 393px;
    background: var(--card-front);
  }
  .card--back {
    left: 253px; top: 536px; width: 694px; height: 396px;
    background: var(--card-back);
  }

  .front-ring {
    position: absolute;
    left: 300px; top: 3px;
    width: 388px; height: 388px;
    border: 13px solid var(--watermark);
    border-radius: 50%;
  }

  .front-info {
    position: absolute;
    left: 0; top: 0;
    width: 344px;
    text-align: center;
    color: var(--ink);
  }
  .firm-name {
    position: absolute; left: 0; width: 344px; top: 34px;
    font-size: 29px; font-weight: 700; letter-spacing: 0.5px;
    white-space: nowrap;
  }
  .person-name {
    position: absolute; left: 0; width: 344px; top: 91px;
    font-size: 33px; font-weight: 700; letter-spacing: 1px;
  }
  .person-role {
    position: absolute; left: 0; width: 344px; top: 134px;
    font-size: 17px; font-weight: 400; letter-spacing: 1px;
    color: var(--ink-soft);
  }
  .contact-icons {
    position: absolute; left: 0; top: 176px; width: 344px; height: 26px;
  }
  .contact-icons .rule {
    position: absolute; top: 13px; height: 2px; background: var(--ink);
  }
  .contact-icons .rule--left { left: 57px; width: 63px; }
  .contact-icons .rule--right { left: 225px; width: 62px; }
  .contact-icons .icon {
    position: absolute; top: 0; width: 26px; height: 26px;
  }
  .contact-line {
    position: absolute; left: 0; width: 344px;
    font-size: 16px; color: var(--ink-soft); letter-spacing: 0.5px;
  }
  .contact-line--phone { top: 222px; font-size: 18px; }
  .contact-line--mail { top: 251px; font-size: 15px; }
  .contact-line--web { top: 278px; font-size: 15px; }
  .divider {
    position: absolute; left: 70px; top: 306px; width: 204px; height: 2px;
    background: var(--ink);
  }
  .address-line {
    position: absolute; left: 0; width: 344px;
    font-size: 17px; color: var(--ink-soft); letter-spacing: 0.5px;
  }
  .address-line--1 { top: 322px; }
  .address-line--2 { top: 350px; }

  .back-ring {
    position: absolute;
    left: 246px; top: 63px;
    width: 210px; height: 210px;
    border: 6px solid var(--white);
    border-radius: 50%;
  }
  .back-firm-name {
    position: absolute; left: 0; width: 694px; top: 295px;
    text-align: center;
    font-size: 38px; font-weight: 700; letter-spacing: 1px;
    color: var(--white);
    white-space: nowrap;
  }
</style>
</head>
<body>
<main class="stage">

  <section class="card card--front" aria-label="Business card front">
    <div class="front-ring" aria-hidden="true"></div>
    <div class="front-info">
      <h1 class="firm-name">Corvane Capital</h1>
      <h2 class="person-name">DANIEL HARTLEY</h2>
      <p class="person-role">Managing Director</p>

      <div class="contact-icons" aria-hidden="true">
        <span class="rule rule--left"></span>
        <svg class="icon" style="left:127px" viewBox="0 0 26 26">
          <rect width="26" height="26" rx="5" fill="#1c1f2e"/>
          <path d="M6 11c0-3 3-5 7-5s7 2 7 5l-3 1-1-2h-6l-1 2z" fill="#fff"/>
          <rect x="7" y="13" width="12" height="7" rx="1.5" fill="#fff"/>
          <g fill="#1c1f2e"><circle cx="10" cy="15" r="0.8"/><circle cx="13" cy="15" r="0.8"/><circle cx="16" cy="15" r="0.8"/><circle cx="10" cy="18" r="0.8"/><circle cx="13" cy="18" r="0.8"/><circle cx="16" cy="18" r="0.8"/></g>
        </svg>
        <svg class="icon" style="left:159px" viewBox="0 0 26 26">
          <rect width="26" height="26" rx="5" fill="#1c1f2e"/>
          <rect x="5" y="8" width="16" height="11" rx="1.5" fill="#fff"/>
          <path d="M5.5 9l7.5 6 7.5-6" fill="none" stroke="#1c1f2e" stroke-width="1.4"/>
        </svg>
        <svg class="icon" style="left:191px" viewBox="0 0 26 26">
          <rect width="26" height="26" rx="5" fill="#1c1f2e"/>
          <circle cx="13" cy="13" r="8" fill="#fff"/>
          <path d="M9 8c2 1 3 3 2 5s-3 1-3 3M15 7c-1 2 1 3 3 3M14 19c0-2 2-3 3-4" fill="none" stroke="#1c1f2e" stroke-width="1.6"/>
        </svg>
        <span class="rule rule--right"></span>
      </div>

      <p class="contact-line contact-line--phone">123 456 789</p>
      <p class="contact-line contact-line--mail">INFO@CORVANEMAIL.COM</p>
      <p class="contact-line contact-line--web">WWW.CORVANECAPITAL.COM</p>
      <div class="divider" aria-hidden="true"></div>
      <p class="address-line address-line--1">Your address, City</p>
      <p class="address-line address-line--2">State, Zip 1234</p>
    </div>
  </section>

  <section class="card card--back" aria-label="Business card back">
    <div class="back-ring" aria-hidden="true"></div>
    <p class="back-firm-name">Corvane Capital</p>
  </section>

</main>
</body>
</html>
```